Business card design needed

OH&S consultancy and training

Industry/Entity Type

Training

Contact Information for Business Card

Coastal Hazard & Learning Collective
Dorian Whitfield
Director

0427 913 058
dorian.whitfield@chlcollect.com.au
chlcollect.com.au

Ph: 03 9172 4039
Fx: 03 9172 4041

```html
<!DOCTYPE html>
<html lang="en">
<head>
<meta charset="utf-8">
<title>CHL Collective – Business Card</title>
<link rel="stylesheet" href="https://fonts.googleapis.com/css2?family=Barlow:wght@400;500;600&display=swap">
<style>
  :root {
    --canvas: #dfe3e5;
    --charcoal: #5b5b5c;
    --charcoal-dark: #3a3a3b;
    --signal-yellow: #ffe600;
    --paper: #ffffff;
    --ink: #2f2f30;
    --muted: #d9d9d9;
  }
  * { box-sizing: border-box; margin: 0; padding: 0; }
  html, body {
    width: 1200px; height: 960px; overflow: hidden;
    background: var(--canvas);
    font-family: "Barlow", Arial, sans-serif;
  }
  .sheet {
    width: 1200px; height: 960px;
    display: flex; flex-direction: column; align-items: center; justify-content: center;
    gap: 60px;
  }
  .card {
    width: 700px; height: 400px;
    box-shadow: 0 10px 30px rgba(0,0,0,.18);
    overflow: hidden;
  }

  /* Front */
  .card-front {
    background: var(--charcoal);
    display: flex; align-items: center; justify-content: center;
  }
  .brand { display: flex; flex-direction: column; align-items: flex-start; }
  .brand-row { display: flex; align-items: center; gap: 18px; }
  .brand-square { width: 46px; height: 46px; background: var(--signal-yellow); }
  .brand-name {
    font-size: 60px; font-weight: 500; letter-spacing: 3px;
    color: var(--muted); line-height: 1;
  }
  .brand-tagline {
    margin-top: 8px; margin-left: 64px;
    font-size: 15px; font-weight: 400; color: var(--charcoal-dark); letter-spacing: .5px;
  }

  /* Back */
  .card-back { display: flex; background: var(--paper); }
  .back-panel {
    width: 200px; background: var(--charcoal);
    border-right: 5px solid var(--signal-yellow);
    position: relative;
  }
  .back-panel .brand {
    position: absolute; left: 50%; top: 50%;
    transform: translate(-50%, -50%) rotate(-90deg);
    white-space: nowrap;
  }
  .back-panel .brand-square { width: 30px; height: 30px; }
  .back-panel .brand-name { font-size: 38px; letter-spacing: 2px; }
  .back-panel .brand-tagline { margin-left: 42px; font-size: 10px; }

  .contact { flex: 1; padding: 46px 44px 0 46px; color: var(--ink); }
  .person-name { font-size: 36px; font-weight: 500; letter-spacing: .5px; }
  .person-role { font-size: 19px; margin-top: 8px; }
  .rule { height: 2px; background: var(--signal-yellow); margin: 24px 0 22px; }
  .phones { list-style: none; font-size: 19px; line-height: 1.3; }
  .phones li { display: flex; gap: 14px; }
  .phone-label { color: var(--signal-yellow); width: 14px; }
  .email { font-size: 19px; }
  .website { font-size: 19px; font-weight: 600; margin-top: 4px; }
</style>
</head>
<body>
<main class="sheet">
  <section class="card card-front" aria-label="Card front">
    <div class="brand">
      <div class="brand-row">
        <span class="brand-square"></span>
        <span class="brand-name">CHL COLLECTIVE</span>
      </div>
      <span class="brand-tagline">Coastal Hazard &amp; Learning Collective</span>
    </div>
  </section>

  <section class="card card-back" aria-label="Card back">
    <div class="back-panel">
      <div class="brand">
        <div class="brand-row">
          <span class="brand-square"></span>
          <span class="brand-name">CHL COLLECTIVE</span>
        </div>
        <span class="brand-tagline">Coastal Hazard &amp; Learning Collective</span>
      </div>
    </div>
    <div class="contact">
      <h1 class="person-name">Dorian Whitfield</h1>
      <p class="person-role">Director</p>
      <div class="rule"></div>
      <ul class="phones">
        <li><span class="phone-label">M</span><span>0427 913 058</span></li>
        <li><span class="phone-label">T</span><span>03 9172 4039</span></li>
        <li><span class="phone-label">F</span><span>03 9172 4041</span></li>
      </ul>
      <div class="rule"></div>
      <p class="email">dorian.whitfield@chlcollect.com.au</p>
      <p class="website">chlcollect.com.au</p>
    </div>
  </section>
</main>
</body>
</html>
```